Kestrel Hiring Homepage Redesign

Redevelopment work is underway on the Kestrel Hiring website www.kestrel-hiring.com - one task is to create a more compelling vertically stacked, mobile friendly homepage. The developers are not graphic designers and have been unable to produce an effective enough design. Their latest iteration can be seen @ http://vantorweb.co.uk/kestrel_hiring/index_5.html

The goal of the current design job is to:

a) produce a homepage design - reworking the attached draft concepts/designs to produce an effective landing page that will entice visitors to respond to the key call to action - to book a meeting with me to discuss their needs
b) ensure the design is aesthetically/functionally aligned with the rest of the site
c) ensure the design supports responsive implementation for viewing on a full range of desktop browsers and mobile devices.

Final output should be in a .psd file with all layers unmerged.

Further details on uploaded docs.

```html
<!DOCTYPE html>
<html lang="en">
<head>
<meta charset="utf-8">
<title>Kestrel Hiring – Online Leadership Coaching &amp; Assessment</title>
<link rel="stylesheet" href="https://fonts.googleapis.com/css2?family=Open+Sans:wght@300;400;600;700&family=Arimo:wght@400;700&display=swap">
<style>
:root{
  --orange:#f07f1a;
  --orange-dark:#e06a0c;
  --arrow:#f4a81c;
  --navy:#1f4f82;
  --blue-btn:#4a87c8;
  --blue-btn-dark:#3a72b0;
  --text:#555;
  --muted:#8a8a8a;
  --line:#e4e4e4;
  --card:#fafafa;
  --dark:#2b2b2b;
  --footer:#0d0d0d;
  --footer-bar:#1a1a1a;
  --white:#fff;
}
*{box-sizing:border-box;margin:0;padding:0}
html,body{width:1200px;height:2462px;overflow:hidden;background:var(--white)}
body{position:relative;font-family:"Open Sans",Arial,sans-serif;color:var(--text)}
h1,h2,h3,h4{font-weight:400}

/* header */
.site-header{position:absolute;left:0;top:0;width:1200px;height:141px;background:var(--white)}
.brand{position:absolute;left:172px;top:30px;display:flex;align-items:center;gap:12px}
.brand-dot{width:40px;height:40px;border-radius:50%;background:var(--orange)}
.brand-name{font-size:34px;font-weight:700;color:var(--navy);letter-spacing:-.5px}
.brand-tag{position:absolute;left:172px;top:106px;font-size:12px;font-style:italic;color:var(--muted)}
.header-phone{position:absolute;right:170px;top:38px;font-size:16px;color:#444}
.header-phone span{color:var(--orange)}
.main-nav{position:absolute;right:170px;top:91px;display:flex;font-size:13px;color:#555}
.main-nav a{color:inherit;text-decoration:none;padding:0 9px;border-left:1px solid #ccc;line-height:14px}
.main-nav a:first-child{border-left:0;color:var(--orange)}
.main-nav a:last-child{padding-right:0}

/* hero */
.hero{position:absolute;left:0;top:141px;width:1200px;height:473px;background:linear-gradient(90deg,#eef7fc 0%,#c7e6f5 40%,#d6eef8 70%,#eef8fc 100%)}
.hero-photo{position:absolute;left:151px;top:14px;width:473px;height:459px;background:linear-gradient(180deg,#c9d5e0 0%,#6b8fc6 55%,#4f73ad 100%);border-radius:200px 200px 0 0}
.hero-links{position:absolute;left:691px;top:58px;width:340px}
.hero-link{display:flex;justify-content:space-between;align-items:center;height:74px;border-bottom:1px solid #b9d4e2;font-size:17px;font-weight:300;color:#5a6770;line-height:24px}
.hero-link svg{flex:none}
.hero-cta-title{position:absolute;left:691px;top:293px;font-size:19px;font-weight:600;color:#3c4d5a}
.btn-book{position:absolute;display:flex;align-items:center;gap:14px;background:linear-gradient(180deg,var(--blue-btn),var(--blue-btn-dark));color:var(--white);text-transform:uppercase;border-radius:2px}
.hero .btn-book{left:691px;top:335px;width:174px;height:53px;padding-left:14px;font-size:12px;font-weight:600;line-height:16px;letter-spacing:.5px}
.hero-dots{position:absolute;left:696px;top:417px;display:flex;gap:5px}
.hero-dots i{width:10px;height:10px;border-radius:50%;background:#d9e6ee;border:1px solid #b9cbd6}
.hero-dots i:first-child{background:var(--navy);border-color:var(--navy)}

/* steps */
.section-title{position:absolute;left:0;width:1200px;text-align:center;font-family:Arimo,Arial,sans-serif;font-weight:400;text-transform:uppercase;letter-spacing:1.5px}
.steps-title{top:642px;font-size:22px;color:var(--navy)}
.step-card{position:absolute;top:705px;width:244px;height:362px;background:var(--card);border:1px solid var(--line)}
.step-name{margin-top:14px;text-align:center;font-size:16px;font-weight:400;line-height:22px;color:#555;letter-spacing:.5px;text-transform:uppercase}
.step-icon{display:block;margin:18px auto 0;width:108px;height:108px}
.step-lead{margin:20px 0 0 19px;font-size:16px;color:var(--navy);line-height:24px}
.step-list{list-style:none;margin:12px 12px 0 19px}
.step-list li{position:relative;padding-left:18px;font-family:Arimo,Arial,sans-serif;font-size:12px;color:var(--muted);line-height:16px;margin-bottom:10px}
.step-list li::before{content:"";position:absolute;left:2px;top:3px;width:4px;height:7px;border:solid var(--orange);border-width:0 2px 2px 0;transform:rotate(45deg)}
.step-arrow{position:absolute;top:803px}

/* audience */
.audience{position:absolute;left:0;top:1111px;width:1200px;height:478px;background:linear-gradient(180deg,#3a3a3a,#262626)}
.audience-title{top:1156px;font-size:21px;color:var(--white);letter-spacing:.5px}
.aud-card{position:absolute;top:1211px;width:269px;height:335px;border:1px solid rgba(255,255,255,.12);text-align:center}
.aud-avatar{width:128px;height:128px;border-radius:50%;margin:22px auto 0;border:4px solid #f2f2f2;background:linear-gradient(180deg,#dfe6ec,#5b6f86)}
.aud-name{margin-top:22px;font-size:15px;font-weight:400;color:#ccc;letter-spacing:.5px}
.aud-quote{margin:16px 22px 0;font-family:Arimo,Arial,sans-serif;font-size:11px;line-height:18px;color:#9a9a9a}
.aud-social{display:flex;justify-content:center;gap:6px;margin-top:16px}
.aud-social i{width:28px;height:28px;border-radius:50%;border:1px solid #888}

/* feature */
.feature-photo{position:absolute;left:172px;top:1609px;width:381px;height:382px;background:linear-gradient(180deg,#d9cfc8 0%,#6e8fc9 50%,#4d6fab 100%);border-radius:180px 180px 0 0}
.feature-video{position:absolute;left:602px;top:1620px;width:427px;height:255px;background:linear-gradient(135deg,#2a2a2a,#3b3b3b);border-radius:3px;box-shadow:0 3px 0 #bbb}
.feature-video .play{position:absolute;left:185px;top:107px;width:58px;height:44px;border-radius:6px;background:rgba(255,255,255,.9)}
.btn-feature{left:602px;top:1904px;width:278px;height:71px;padding-left:22px;font-size:21px;font-weight:300;line-height:24px}

/* footer */
.site-footer{position:absolute;left:0;top:1991px;width:1200px;height:394px;background:linear-gradient(180deg,#111,#050505)}
.footer-title{position:absolute;left:0;top:2025px;width:1200px;text-align:center;font-size:26px;font-weight:300;color:#ddd}
.footer-sub{position:absolute;left:0;top:2074px;width:1200px;text-align:center;font-family:Arimo,Arial,sans-serif;font-size:14px;color:#aaa}
.office{position:absolute;left:172px;top:2134px;width:250px;height:227px;border:1px solid #333;padding:14px 20px}
.office .brand-name{font-size:20px;color:var(--orange)}
.office-brand{display:flex;align-items:center;gap:8px}
.office-brand .brand-dot{width:22px;height:22px}
.office h3{margin-top:14px;font-size:16px;color:#ccc;letter-spacing:.5px}
.office address{margin-top:12px;font-style:normal;font-size:12px;line-height:18px;color:#888}
.office-line{display:flex;align-items:center;gap:12px;margin-top:12px;font-size:12px;color:#aaa}
.footer-info h4,.footer-map h4{font-size:15px;color:#ccc}
.footer-info{position:absolute;left:481px;top:2134px}
.footer-info ul{list-style:none;margin-top:16px}
.footer-info li{font-size:11px;color:#aaa;line-height:24px}
.footer-map{position:absolute;left:657px;top:2124px}
.map-fill{margin-top:12px;width:372px;height:169px;background:linear-gradient(135deg,#f1eadb,#dde6c7 50%,#c9d6e3)}
.footer-bar{position:absolute;left:0;top:2385px;width:1200px;height:77px;background:var(--footer-bar)}
.copyright{position:absolute;left:174px;top:32px;font-size:11px;color:#888}
.bar-social{position:absolute;top:18px;width:36px;height:36px;border-radius:50%;border:2px solid #666}
.to-top{position:absolute;left:983px;top:15px;width:46px;height:46px;border-radius:50%;background:#2a2a2a}
</style>
</head>
<body>

<header class="site-header">
  <div class="brand"><span class="brand-dot"></span><span class="brand-name">Kestrel Hiring</span></div>
  <div class="brand-tag">Online Leadership Coaching &amp; Assessment</div>
  <div class="header-phone">Phone: <span>+1 555 014 2290</span></div>
  <nav class="main-nav">
    <a href="#">Transforming Leadership</a>
    <a href="#">Assesments</a>
    <a href="#">Coaching</a>
    <a href="#">Resources &amp; Tools</a>
    <a href="#">Bookings &amp; Prices</a>
  </nav>
</header>

<section class="hero">
  <div class="hero-photo" role="img" aria-label="Leadership coach in a blue shirt and patterned tie, gesturing while speaking"></div>
  <div class="hero-links">
    <div class="hero-link"><span>Sign up for the latest emotional<br>leadership resources and tools</span><svg width="16" height="40" viewBox="0 0 16 40"><path d="M2 2 L14 20 L2 38" fill="none" stroke="#7a8a95" stroke-width="1.5"/></svg></div>
    <div class="hero-link"><span>Learn how leadership assessments<br>help the coaching process</span><svg width="16" height="40" viewBox="0 0 16 40"><path d="M2 2 L14 20 L2 38" fill="none" stroke="#7a8a95" stroke-width="1.5"/></svg></div>
    <div class="hero-link"><span>Are you ready for the leadership<br>litmus test?</span><svg width="16" height="40" viewBox="0 0 16 40"><path d="M2 2 L14 20 L2 38" fill="none" stroke="#7a8a95" stroke-width="1.5"/></svg></div>
  </div>
  <div class="hero-cta-title">Kestrel Hiring Can Help...</div>
  <a class="btn-book">
    <svg width="30" height="28" viewBox="0 0 30 28" fill="#fff"><circle cx="8" cy="5" r="4"/><circle cx="22" cy="5" r="4"/><rect x="3" y="11" width="10" height="9" rx="2"/><rect x="17" y="11" width="10" height="9" rx="2"/><rect x="0" y="20" width="30" height="3"/><rect x="6" y="23" width="2" height="5"/><rect x="22" y="23" width="2" height="5"/></svg>
    <span>Book a<br>Meeting Now</span>
  </a>
  <div class="hero-dots"><i></i><i></i><i></i><i></i></div>
</section>

<h2 class="section-title steps-title">Steps to Leadership Success</h2>

<article class="step-card" style="left:171px">
  <h3 class="step-name">Partner &amp; Plan</h3>
  <svg class="step-icon" viewBox="0 0 108 108"><circle cx="54" cy="54" r="54" fill="var(--orange)"/><path d="M26 50 L40 38 L54 44 L68 38 L82 50 L66 68 L48 70 Z" fill="#fff"/><path d="M40 56 L52 66 M46 52 L58 62 M54 48 L64 58" stroke="var(--orange)" stroke-width="3"/></svg>
  <p class="step-lead">With An Experienced<br>Leadership Coach To:</p>
  <ul class="step-list">
    <li>CLARIFY, desired goals and commitment</li>
    <li>ASSESS strengths and development opportunities</li>
    <li>DEFINE leadership coaching plan</li>
  </ul>
</article>
<svg class="step-arrow" style="left:415px" width="54" height="46" viewBox="0 0 54 46"><path d="M0 12 H26 V0 L54 23 L26 46 V34 H0 Z" fill="var(--arrow)"/></svg>
<article class="step-card" style="left:479px">
  <h3 class="step-name">Work the Plan</h3>
  <svg class="step-icon" viewBox="0 0 108 108"><circle cx="54" cy="54" r="54" fill="var(--orange)"/><rect x="36" y="28" width="36" height="50" fill="#fff"/><rect x="42" y="34" width="14" height="10" fill="none" stroke="var(--orange)" stroke-width="2"/><path d="M42 52 H66 M42 58 H66 M42 64 H66 M42 70 H60" stroke="var(--orange)" stroke-width="2"/></svg>
  <p class="step-lead">Daily Practice To Build<br>And Refine Skills To:</p>
  <ul class="step-list">
    <li>EXPLORE new perspectives</li>
    <li>EXPERIMENT with new ways of doing things</li>
    <li>EMBED new skills until natural and habitual</li>
  </ul>
</article>
<svg class="step-arrow" style="left:722px" width="54" height="46" viewBox="0 0 54 46"><path d="M0 12 H26 V0 L54 23 L26 46 V34 H0 Z" fill="var(--arrow)"/></svg>
<article class="step-card" style="left:786px">
  <h3 class="step-name">Take Stock</h3>
  <svg class="step-icon" viewBox="0 0 108 108"><circle cx="54" cy="54" r="54" fill="var(--orange)"/><g fill="#fff"><rect x="32" y="40" width="12" height="12"/><rect x="47" y="40" width="12" height="12"/><rect x="62" y="32" width="12" height="12" transform="rotate(15 68 38)"/><rect x="32" y="55" width="12" height="12"/><rect x="47" y="55" width="12" height="12"/><rect x="62" y="55" width="12" height="12"/><rect x="47" y="70" width="12" height="10"/><rect x="62" y="70" width="12" height="10"/></g></svg>
  <p class="step-lead">Regular Review Of Prog-<br>ress To:</p>
  <ul class="step-list">
    <li>ASSESS progress</li>
    <li>REFINE the plan</li>
    <li>CELEBRATE success</li>
  </ul>
</article>

<section class="audience" role="img" aria-label="Dimmed photo of a business meeting behind the section"></section>
<h2 class="section-title audience-title">Who is leadership assessment and coaching for?</h2>

<article class="aud-card" style="left:171px">
  <div class="aud-avatar" role="img" aria-label="Portrait of an organisational leader"></div>
  <h3 class="aud-name">Organisational Leaders</h3>
  <p class="aud-quote">I really appreciate the great work Tom did with me to get my focus back on leading the business through a difficult change process. It definitely</p>
  <div class="aud-social"><i></i><i></i><i></i><i></i></div>
</article>
<article class="aud-card" style="left:469px">
  <div class="aud-avatar" role="img" aria-label="Portrait of an HR and OD manager"></div>
  <h3 class="aud-name">HR &amp; OD Manager</h3>
  <p class="aud-quote">I really appreciate the great work Tom did with me to get my focus back on leading the business through a difficult change process. It definitely</p>
  <div class="aud-social"><i></i><i></i><i></i><i></i></div>
</article>
<article class="aud-card" style="left:763px">
  <div class="aud-avatar" role="img" aria-label="Portrait of a team leader"></div>
  <h3 class="aud-name">Team Leaders</h3>
  <p class="aud-quote">I really appreciate the great work Tom did with me to get my focus back on leading the business through a difficult change process. It definitely</p>
  <div class="aud-social"><i></i><i></i><i></i><i></i></div>
</article>

<div class="feature-photo" role="img" aria-label="Coach in a blue shirt with hands pressed together"></div>
<div class="feature-video" role="img" aria-label="Video thumbnail: teamwork illustration of coloured gears with the coach">
  <span class="play"><svg width="58" height="44" viewBox="0 0 58 44"><path d="M23 13 L37 22 L23 31 Z" fill="#333"/></svg></span>
</div>
<a class="btn-book btn-feature">
  <svg width="40" height="36" viewBox="0 0 30 28" fill="#fff"><circle cx="8" cy="5" r="4"/><circle cx="22" cy="5" r="4"/><rect x="3" y="11" width="10" height="9" rx="2"/><rect x="17" y="11" width="10" height="9" rx="2"/><rect x="0" y="20" width="30" height="3"/><rect x="6" y="23" width="2" height="5"/><rect x="22" y="23" width="2" height="5"/></svg>
  <span>Book a<br>Meeting Now</span>
</a>

<footer class="site-footer"></footer>
<h2 class="footer-title">Contact us</h2>
<p class="footer-sub">To book an appointment with one of our Advisors, please contact one of our offices:</p>
<div class="office">
  <div class="office-brand"><span class="brand-dot"></span><span class="brand-name">Kestrel Hiring</span></div>
  <h3>Corporate Office</h3>
  <address>48 Harrow Lane London,<br>United Kingdom NW2 4QP</address>
  <div class="office-line"><svg width="18" height="18" viewBox="0 0 18 18"><path d="M4 1 L7 5 L5 7 Q7 11 11 13 L13 11 L17 14 L15 17 Q6 16 1 4 Z" fill="none" stroke="var(--orange)" stroke-width="1.5"/></svg>+44 20 5550 1847</div>
  <div class="office-line"><svg width="18" height="14" viewBox="0 0 18 14"><rect x="1" y="1" width="16" height="12" fill="none" stroke="var(--orange)" stroke-width="1.5"/><path d="M1 1 L9 8 L17 1" fill="none" stroke="var(--orange)" stroke-width="1.5"/></svg>tom@kestrel-hiring.com</div>
</div>
<div class="footer-info">
  <h4>information</h4>
  <ul>
    <li>Home</li><li>Transforming Leadership</li><li>Assesments</li><li>Coaching</li><li>Resources &amp; Tools</li><li>Bookings &amp; Prices</li><li>About</li>
  </ul>
</div>
<div class="footer-map">
  <h4>Our Location</h4>
  <div class="map-fill" role="img" aria-label="Street map showing the office location"></div>
</div>

<div class="footer-bar">
  <p class="copyright">© 2013 Kestrel Hiring. All rights reserved.</p>
  <span class="bar-social" style="left:584px"></span>
  <span class="bar-social" style="left:655px"></span>
  <span class="bar-social" style="left:727px"></span>
  <span class="to-top"><svg width="46" height="46" viewBox="0 0 46 46"><path d="M17 26 L23 20 L29 26" fill="none" stroke="#555" stroke-width="2"/></svg></span>
</div>

</body>
</html>
```